Business Card Design Project

Actor, Producer, Vocal Coach, Choral Director, Song WriterPhone: (215) 555-0142 Fax: (215) 856-3933Email: waltierblocker@gmail.comFacebook: facebook.com/waltier.blockerTwitter: @thedf482

Industry/Entity Type

Business

Contact Information for Business Card

Business Cards that include my picture

Colors

Designer to choose colors to be used in the design.

```html
<!DOCTYPE html>
<html lang="en">
<head>
<meta charset="utf-8">
<title>Dorian Fellsmore – Business Card</title>
<link rel="stylesheet" href="https://fonts.googleapis.com/css2?family=Ubuntu:wght@500&family=Open+Sans:wght@300;400&display=swap">
<style>
  :root {
    --page-bg: #ecebe8;
    --card-top: #ffffff;
    --card-bottom: #eeeeee;
    --accent-pink: #e2639f;
    --text-gray: #6b6b6b;
    --text-dark: #3d3d3d;
    --photo-core: #e6e4ea;
    --photo-blush: #f3dbe6;
  }
  * { margin: 0; padding: 0; box-sizing: border-box; }
  html, body {
    width: 1200px;
    height: 1023px;
    overflow: hidden;
    background: var(--page-bg);
  }
  .business-card {
    position: absolute;
    left: 100px;
    top: 226px;
    width: 1000px;
    height: 571px;
    border-radius: 26px;
    background: linear-gradient(160deg, var(--card-top) 0%, var(--card-top) 45%, var(--card-bottom) 100%);
    box-shadow: 0 10px 30px rgba(0, 0, 0, 0.12);
    overflow: hidden;
  }
  .portrait-photo {
    position: absolute;
    left: 20px;
    top: 200px;
    width: 500px;
    height: 371px;
    background:
      radial-gradient(ellipse closest-side at 55% 60%, var(--photo-blush) 0%, rgba(243, 219, 230, 0) 70%),
      radial-gradient(ellipse closest-side at 45% 55%, var(--photo-core) 0%, rgba(230, 228, 234, 0.6) 55%, rgba(230, 228, 234, 0) 100%);
  }
  .contact-block {
    position: absolute;
    left: 520px;
    top: 92px;
  }
  .person-name {
    font-family: "Ubuntu", sans-serif;
    font-weight: 500;
    font-size: 50px;
    color: var(--accent-pink);
    letter-spacing: 0.5px;
    line-height: 1.1;
  }
  .person-roles {
    margin-top: 8px;
    font-family: "Open Sans", sans-serif;
    font-weight: 300;
    font-size: 24px;
    line-height: 1.35;
    color: var(--text-gray);
  }
  .contact-list {
    list-style: none;
    margin-top: 26px;
  }
  .contact-item {
    display: flex;
    align-items: center;
    gap: 14px;
    font-family: "Open Sans", sans-serif;
    font-weight: 400;
    font-size: 22px;
    line-height: 1.5;
    color: var(--text-dark);
  }
  .contact-icon {
    width: 18px;
    height: 18px;
    flex: none;
    fill: var(--accent-pink);
  }
</style>
</head>
<body>
  <article class="business-card">
    <div class="portrait-photo" role="img" aria-label="Portrait photo of the performer in a white shirt and pink tie"></div>

    <section class="contact-block">
      <h1 class="person-name">Dorian Fellsmore</h1>
      <p class="person-roles">Actor, Producer, Vocal Coach,<br>Choral Director, Song Writer</p>

      <ul class="contact-list">
        <li class="contact-item">
          <svg class="contact-icon" viewBox="0 0 24 24" aria-hidden="true"><path d="M6.6 10.8a15.1 15.1 0 0 0 6.6 6.6l2.2-2.2a1 1 0 0 1 1-.25 11.4 11.4 0 0 0 3.6.57 1 1 0 0 1 1 1V20a1 1 0 0 1-1 1A17 17 0 0 1 3 4a1 1 0 0 1 1-1h3.5a1 1 0 0 1 1 1c0 1.25.2 2.45.57 3.6a1 1 0 0 1-.25 1z"/></svg>
          (215) 555-0142
        </li>
        <li class="contact-item">
          <svg class="contact-icon" viewBox="0 0 24 24" aria-hidden="true"><rect x="6" y="2" width="12" height="6"/><rect x="2" y="9" width="20" height="9" rx="2"/><rect x="6" y="15" width="12" height="7" fill="#fff" stroke="#e2639f" stroke-width="2"/></svg>
          (215) 555-0187
        </li>
        <li class="contact-item">
          <svg class="contact-icon" viewBox="0 0 24 24" aria-hidden="true"><rect x="2" y="5" width="20" height="14" rx="1" fill="none" stroke="#e2639f" stroke-width="2"/><path d="M3 6l9 7 9-7" fill="none" stroke="#e2639f" stroke-width="2"/></svg>
          dorianfellsmore@postlane.net
        </li>
        <li class="contact-item">
          <svg class="contact-icon" viewBox="0 0 24 24" aria-hidden="true"><circle cx="12" cy="12" r="8"/></svg>
          socialpage.net/dorian.fellsmore
        </li>
        <li class="contact-item">
          <svg class="contact-icon" viewBox="0 0 24 24" aria-hidden="true"><circle cx="12" cy="12" r="8"/></svg>
          @thedf482
        </li>
      </ul>
    </section>
  </article>
</body>
</html>
```